New Business Card Design

We would like to refresh our business cards and make them look better. We are an IT company specialising in Cloud Services, IT Managed Services, software and hardware. I have attached a PSD of our current design. Also attached our logo.
Updates

I have uploaded all new logos in EPS format.

Can you please edit all designs to include a job title for Marcus Hollis, eg. General Manager

Industry/Entity Type

Software

Colors
ffffff

Requirements
Must have
• Please use white background.
Should not have
• Black background

```html
<!DOCTYPE html>
<html lang="en">
<head>
<meta charset="utf-8">
<title>Quillveth Networks – Business Cards</title>
<link rel="stylesheet" href="https://fonts.googleapis.com/css2?family=Open+Sans:wght@300;400;600;700&display=swap">
<style>
  :root {
    --page: #eceef0;
    --card-light: #f7f8f9;
    --card-mid: #e3e5e8;
    --card-edge: #d4d7db;
    --ink: #2b2d30;
    --ink-soft: #55595e;
    --accent: #d4412b;
    --band-grey: #a9b1ba;
    --divider: #b9bec4;
  }
  * { box-sizing: border-box; margin: 0; padding: 0; }
  html, body { width: 1200px; height: 720px; overflow: hidden; }
  body {
    background: var(--page);
    font-family: "Open Sans", Arial, sans-serif;
    color: var(--ink);
    display: flex;
    align-items: center;
    justify-content: center;
    gap: 40px;
  }
  .card {
    position: relative;
    width: 540px;
    height: 310px;
    background: linear-gradient(135deg, var(--card-light) 0%, var(--card-mid) 45%, var(--card-light) 70%, var(--card-mid) 100%);
    border: 1px solid var(--card-edge);
    box-shadow: 0 6px 18px rgba(0,0,0,0.12);
    overflow: hidden;
  }
  .brand {
    position: absolute;
    display: flex;
    align-items: center;
    gap: 12px;
  }
  .brand-dot {
    border-radius: 50%;
    background: var(--accent);
    flex: none;
  }
  .brand-name {
    font-weight: 300;
    color: var(--ink);
    letter-spacing: 0.12em;
    line-height: 1;
    white-space: nowrap;
  }
  /* front */
  .card-front .brand { left: 70px; top: 64px; }
  .card-front .brand-dot { width: 42px; height: 42px; }
  .card-front .brand-name { font-size: 26px; }
  .person {
    position: absolute;
    right: 282px;
    top: 158px;
    text-align: right;
  }
  .person-name { color: var(--accent); font-weight: 700; font-size: 17px; }
  .person-title { font-weight: 600; font-size: 12px; margin-top: 2px; }
  .contact-divider {
    position: absolute;
    left: 270px;
    top: 150px;
    width: 1px;
    height: 82px;
    background: var(--divider);
  }
  .contact-list {
    position: absolute;
    left: 284px;
    top: 150px;
    list-style: none;
  }
  .contact-row, .person-mobile {
    display: flex;
    align-items: center;
    gap: 7px;
    font-size: 12.5px;
    color: var(--ink-soft);
    line-height: 24px;
  }
  .person-mobile { justify-content: flex-end; margin-top: 6px; }
  .icon { width: 12px; height: 12px; flex: none; }
  .card-bands { position: absolute; left: 0; bottom: 0; }
  /* back */
  .card-back .brand { left: 0; right: 0; top: 108px; justify-content: center; }
  .card-back .brand-dot { width: 48px; height: 48px; }
  .card-back .brand-name { font-size: 28px; }
  .back-web {
    position: absolute;
    left: 0; right: 0;
    top: 212px;
    text-align: center;
    font-size: 16px;
    letter-spacing: 0.16em;
    color: var(--ink-soft);
  }
</style>
</head>
<body>
  <section class="card card-front" aria-label="Business card front">
    <div class="brand">
      <span class="brand-dot"></span>
      <span class="brand-name">quillveth networks</span>
    </div>

    <div class="person">
      <p class="person-name">Marcus Hollis</p>
      <p class="person-title">General Manager</p>
      <p class="person-mobile">
        <svg class="icon" viewBox="0 0 12 12" aria-hidden="true"><rect x="3" y="0.5" width="6" height="11" rx="1.2" fill="var(--accent)"/><rect x="4.2" y="2" width="3.6" height="6" fill="#fff"/></svg>
        0491 570 110
      </p>
    </div>

    <div class="contact-divider"></div>

    <ul class="contact-list">
      <li class="contact-row">
        <svg class="icon" viewBox="0 0 12 12" aria-hidden="true"><circle cx="6" cy="6" r="6" fill="var(--accent)"/><path d="M4 3.2 L5.2 3 L5.8 4.6 L5 5.2 Q5.6 6.6 6.8 7 L7.4 6.2 L9 6.8 L8.8 8 Q6 8.4 3.8 5 Z" fill="#fff"/></svg>
        07 5550 1234
      </li>
      <li class="contact-row">
        <svg class="icon" viewBox="0 0 12 12" aria-hidden="true"><circle cx="6" cy="6" r="6" fill="var(--accent)"/><rect x="3" y="4" width="6" height="4.2" fill="#fff"/><path d="M3 4 L6 6.4 L9 4" stroke="var(--accent)" stroke-width="0.8" fill="none"/></svg>
        hollism@quillveth.com.au
      </li>
      <li class="contact-row">
        <svg class="icon" viewBox="0 0 12 12" aria-hidden="true"><circle cx="6" cy="6" r="6" fill="var(--accent)"/><circle cx="6" cy="6" r="3.2" stroke="#fff" stroke-width="0.8" fill="none"/><path d="M2.8 6 H9.2 M6 2.8 V9.2" stroke="#fff" stroke-width="0.7"/></svg>
        www.quillveth.com.au
      </li>
    </ul>

    <svg class="card-bands" width="540" height="80" viewBox="0 0 540 80" aria-hidden="true">
      <polygon points="0,64 250,64 292,36 540,36 540,80 0,80" fill="var(--band-grey)"/>
      <polygon points="232,64 282,30 540,30 540,46 300,46 262,64" fill="var(--accent)"/>
    </svg>
  </section>

  <section class="card card-back" aria-label="Business card back">
    <div class="brand">
      <span class="brand-dot"></span>
      <span class="brand-name">quillveth networks</span>
    </div>
    <p class="back-web">www.quillveth.com.au</p>
  </section>
</body>
</html>
```